Maple Bus Card

i own a building in the bronx ny - its called "Maple 7 on 2 HDFC"i want a classy logo / business card - nothing too religuous but it is like a family there - its a large apartment building - colors i like dark red, black, medium shade of gray also reg business card stuff tel # 914-555-0173 address 4738 Larkwell Ave Bronx NY 10460 Email fijosh@aol.comslogan - " from many we are one "i can send u a picture of the building for the backside

```html
<!DOCTYPE html>
<html lang="en">
<head>
<meta charset="UTF-8">
<title>Maple 7 on 2 HDFC – Business Card</title>
<link rel="stylesheet" href="https://fonts.googleapis.com/css2?family=Open+Sans:wght@400;700&family=Roboto+Condensed:wght@600&display=swap">
<style>
  :root {
    --backdrop: #9b9b9b;
    --card-white: #ffffff;
    --brand-red: #d20a0a;
    --ink: #2b2b2b;
    --mark-dark: #2e2e2e;
    --rule: #d6d6d6;
    --rule-light: rgba(255, 255, 255, 0.45);
  }
  * { margin: 0; padding: 0; box-sizing: border-box; }
  html, body {
    width: 1200px;
    height: 900px;
    overflow: hidden;
    background: var(--backdrop);
    font-family: "Open Sans", sans-serif;
  }
  .canvas { position: relative; width: 1200px; height: 900px; }

  .card { position: absolute; width: 478px; height: 296px; }
  .card-front {
    left: 120px; top: 274px;
    background: var(--card-white);
    border-radius: 0 46px 0 46px;
  }
  .card-back {
    left: 606px; top: 273px;
    background: var(--brand-red);
    border-radius: 46px 0 46px 0;
  }

  .brand-square {
    position: absolute;
    width: 76px; height: 76px;
  }
  .card-front .brand-square { left: 289px; top: 40px; background: var(--mark-dark); }
  .card-back .brand-square { left: 201px; top: 56px; background: var(--card-white); }

  .brand-name {
    position: absolute;
    font-weight: 700;
    white-space: nowrap;
    letter-spacing: -0.2px;
  }
  .card-front .brand-name {
    right: 28px; top: 132px;
    font-size: 26px;
    color: var(--brand-red);
  }
  .card-back .brand-name {
    left: 0; right: 0; top: 150px;
    text-align: center;
    font-size: 28px;
    color: var(--card-white);
  }

  .holder-name {
    position: absolute; left: 30px; top: 182px;
    font-size: 15px; font-weight: 700;
    color: var(--brand-red);
    letter-spacing: 0.2px;
  }
  .holder-title {
    position: absolute; left: 30px; top: 200px;
    font-size: 13.5px; color: var(--ink);
  }
  .title-rule {
    position: absolute; left: 160px; right: 28px; top: 211px;
    height: 1px; background: var(--rule);
  }

  .contact-list {
    position: absolute; left: 30px; top: 234px;
    list-style: none;
    font-size: 13.5px; line-height: 17px; color: var(--ink);
  }
  .contact-list li { display: flex; align-items: center; gap: 4px; }
  .contact-list svg { width: 11px; height: 11px; fill: var(--brand-red); }

  .address {
    position: absolute; right: 28px; top: 234px;
    text-align: right; font-style: normal;
    font-size: 13.5px; line-height: 17px; color: var(--ink);
  }

  .slogan-rule {
    position: absolute; left: 114px; right: 116px; top: 213px;
    height: 1px; background: var(--rule-light);
  }
  .slogan {
    position: absolute; left: 0; right: 0; top: 222px;
    text-align: center;
    font-family: "Roboto Condensed", sans-serif;
    font-weight: 600; font-size: 21.5px;
    color: var(--card-white);
  }
</style>
</head>
<body>
<main class="canvas">
  <section class="card card-front" aria-label="Business card front">
    <div class="brand-square" role="img" aria-label="Brand mark area"></div>
    <div class="brand-name">Maple 7 on 2 HDFC</div>
    <div class="holder-name">MARCUS BELLAMY</div>
    <div class="holder-title">Managing Director</div>
    <div class="title-rule"></div>
    <ul class="contact-list">
      <li>
        <svg viewBox="0 0 12 12" aria-hidden="true"><path d="M1 4.2C1 2.5 3.2 1.5 6 1.5s5 1 5 2.7v.8H8.6v-1H3.4v1H1z M3 6.2l1.4-1.6h3.2L9 6.2v4.3H3z"/></svg>
        914-555-0173
      </li>
      <li>
        <svg viewBox="0 0 12 12" aria-hidden="true"><path d="M1 2.5h10v7H1z" /><path d="M1 2.5l5 4 5-4" fill="none" stroke="#fff" stroke-width="1"/></svg>
        mavreld@quintmail.com
      </li>
    </ul>
    <address class="address">4738 Larkwell Ave<br>Bronx NY 10460</address>
  </section>

  <section class="card card-back" aria-label="Business card back">
    <div class="brand-square" role="img" aria-label="Brand mark area"></div>
    <div class="brand-name">Maple 7 on 2 HDFC</div>
    <div class="slogan-rule"></div>
    <p class="slogan">From many we are one</p>
  </section>
</main>
</body>
</html>
```